Design a landing page

We have a logo, we have colours in mind. What we need is to create a typical one-page landing page that would look nicely on both PC and mobile devices/tablets.

Typical layout - logo top left, top right - shop/client area buttons (links will open to different websites), informational area in the middle - image on the left + text on the right then image on the right + text on the left etc., then text links at the bottom (T&S, Cookie policy, privacy policy etc.).

Page must have cookie notification as per EU law.

We will also need help in preparing photos/images (up to 8) for the website.

End result should be either a Wordpress theme (preferred - so we can install it from wordpress control panel) or HTML/CSS page source. All scripts/images/files should be included - no external links to js/image libraries please.

The photo of the device attached. Primary users will be home users with placement on the ceiling, Minority of users will be business/commercial users with wall placements. Device is meant to monitor climat in the premises (Temperature, humidity, dew point) and alert users if readings are not within allowed range.

Industry/Entity Type

Microclimate Monitoring in premises

Coding

Coded - Design and coding required

Number of Pages Required

1 page

Colors
0054AA
0677BA
7BADD7
CADEEF
E8F1F8
0094D4
00A9DD
6FCCEA
C7EBF8
E9F6FB

Requirements
Must have
• White background, layout as described unless better option offered and accepted. Must have cookie warning.

```html
<!DOCTYPE html>
<html lang="en">
<head>
<meta charset="utf-8">
<title>VELUMIX — Microclimate Monitoring</title>
<link href="https://fonts.googleapis.com/css2?family=Inter:wght@400;500;600;700;800&display=swap" rel="stylesheet">
<style>
:root{
  --navy:#0f2a4f;
  --teal:#3bb4bf;
  --label:#6b9bca;
  --text:#4a5563;
  --panel:#e9f0f7;
  --line:#e6ebf0;
  --white:#ffffff;
}
*{margin:0;padding:0;box-sizing:border-box}
html,body{width:673px;height:1200px;overflow:hidden;background:var(--white);font-family:"Inter",sans-serif;color:var(--navy)}
.page{position:relative;width:673px;height:1200px}
.abs{position:absolute}
.header{left:0;top:0;width:673px;height:27px;border-bottom:1px solid var(--line);background:var(--white)}
.brand{left:128px;top:6px;font-weight:800;font-size:9px;letter-spacing:.2px;color:var(--navy);line-height:14px}
.btn{display:flex;align-items:center;justify-content:center;border-radius:20px;font-weight:500;white-space:nowrap}
.btn-outline{border:1px solid var(--navy);color:var(--navy);background:var(--white)}
.btn-solid{background:var(--navy);color:var(--white)}
.client{left:456px;top:4.5px;width:45px;height:16px;font-size:5px}
.shop{left:505px;top:4.5px;width:43px;height:16px;font-size:5px}
.hero-photo{left:300px;top:27px;width:373px;height:298px;
  background:linear-gradient(90deg,#ffffff 0%,rgba(255,255,255,.6) 25%,rgba(255,255,255,0) 55%),
             linear-gradient(180deg,#eef1f4 0%,#dde3e8 45%,#c9d0d6 100%)}
.device{left:99px;top:95px;width:140px;height:159px;border-radius:26px;
  background:radial-gradient(circle at 40% 35%,#2a2a2c 0%,#0c0c0d 70%);box-shadow:0 8px 20px rgba(0,0,0,.15)}
.eyebrow{font-size:5px;font-weight:600;letter-spacing:1.2px;color:var(--teal);text-transform:uppercase;line-height:6px}
.hero-eyebrow{left:270px;top:108px}
.hero-title{left:270px;top:119px;font-size:19.5px;font-weight:800;letter-spacing:-.3px;line-height:24px;white-space:nowrap}
.hero-copy{left:270px;top:149px;width:230px;font-size:6.1px;line-height:9.8px;color:var(--text)}
.stat-value{font-size:7.6px;font-weight:600;color:var(--navy);line-height:9px}
.stat-label{font-size:4.3px;font-weight:500;color:var(--label);letter-spacing:.2px;text-transform:uppercase;margin-top:2px}
.hero-stats{left:270px;top:192px;display:flex;gap:9px}
.discover{left:270px;top:224px;width:86px;height:21px;font-size:6px;box-shadow:0 4px 8px rgba(15,42,79,.2)}
.panel{left:91px;width:491px;height:238px;border-radius:19px;background:var(--panel)}
.feature-photo{left:134px;width:182px;height:182px;border-radius:5px;box-shadow:0 6px 14px rgba(15,42,79,.12)}
.photo-ceiling{top:379px;background:linear-gradient(160deg,#9a9890 0%,#d8d9d4 45%,#cfd0cc 100%)}
.photo-wall{top:628px;background:linear-gradient(90deg,#dedcd6 0%,#e4e2dc 40%,#8a2e2a 41%,#3a3a45 75%,#2a3450 100%)}
.photo-alert{top:881px;background:linear-gradient(180deg,#caa24d 0%,#c89a45 42%,#2a2a1e 50%,#cdb86b 56%,#c0c4cc 62%,#dadfe6 100%)}
.feature-text{left:340px;width:215px;text-align:center}
.feature-title{font-size:13px;font-weight:800;letter-spacing:-.2px;line-height:15.5px;margin-top:5px}
.feature-copy{font-size:6px;line-height:9.8px;color:var(--text);margin-top:8px}
.feature-stats{display:flex;justify-content:center;gap:9px;margin-top:10px}
.small-btn{display:inline-flex;margin-top:10px;height:18px;padding:0 10px;font-size:5px}
.solid-btn{display:inline-flex;margin-top:12px;height:20px;padding:0 12px;font-size:5.7px}
.footer-line{left:0;top:1112px;width:673px;height:1px;background:var(--line)}
.footer-links{left:0;top:1134px;width:673px;display:flex;justify-content:center;gap:11px;font-size:5px;font-weight:500;color:var(--navy)}
.copyright{left:113px;top:1150px;font-size:4.3px;color:var(--label)}
.cookie{left:197px;top:1165px;width:280px;height:30px;border:1px solid var(--line);border-radius:5px;background:var(--white);box-shadow:0 2px 10px rgba(0,0,0,.05)}
.cookie-text{left:10px;top:8px;width:200px;font-size:4.6px;line-height:7.8px;color:var(--text)}
.cookie-text a{color:var(--teal)}
.accept{left:229px;top:8px;width:40px;height:12px;border-radius:2px;font-size:4.5px;font-weight:600}
</style>
</head>
<body>
<div class="page">
  <header class="abs header">
    <div class="abs brand">VELUMIX</div>
    <a class="abs btn btn-outline client">Client Area</a>
    <a class="abs btn btn-solid shop">Shop Now</a>
  </header>

  <div class="abs hero-photo" role="img" aria-label="Bright modern office lounge with white sofas and city windows"></div>
  <div class="abs device" role="img" aria-label="Black hexagonal monitoring device"></div>
  <div class="abs eyebrow hero-eyebrow">Next-Gen Microclimate Control</div>
  <h1 class="abs hero-title">Precision You Can Feel.</h1>
  <p class="abs hero-copy">Experience absolute control over your environment with our state-of-the-art microclimate monitoring device. Designed for professional oversight in modern homes and business environments.</p>
  <div class="abs hero-stats">
    <div><div class="stat-value">0.1°C</div><div class="stat-label">Temp Accuracy</div></div>
    <div><div class="stat-value">±2%</div><div class="stat-label">RH Precision</div></div>
    <div><div class="stat-value">24/7</div><div class="stat-label">Monitoring</div></div>
  </div>
  <a class="abs btn btn-solid discover">Discover the Device</a>

  <section class="abs panel" style="top:345px"></section>
  <div class="abs feature-photo photo-ceiling" role="img" aria-label="Hand touching a white device mounted on a ceiling beside a pendant lamp"></div>
  <div class="abs feature-text" style="top:411px">
    <div class="eyebrow">Elegant Integration</div>
    <h2 class="feature-title">Seamlessly Blends Into Your Space.</h2>
    <p class="feature-copy">Technology shouldn't intrude; it should integrate. Whether mounted on a living room wall or suspended from a commercial warehouse ceiling, the sleek profile ensure the device looks as good as it performs.</p>
    <a class="btn btn-outline small-btn">View Technical Specs</a>
  </div>

  <div class="abs feature-photo photo-wall" role="img" aria-label="Black device mounted on a brick wall in a warehouse"></div>
  <div class="abs feature-text" style="top:655px">
    <div class="eyebrow">Deep Data Insights</div>
    <h2 class="feature-title">Comprehensive Analytics.</h2>
    <p class="feature-copy">Dive deep into your environmental data. Our intuitive dashboard provides real-time insights, historical charts, and exportable reports, giving you complete visibility over your microclimate.</p>
    <div class="feature-stats">
      <div><div class="stat-value">Unlimited</div><div class="stat-label">Data History</div></div>
      <div><div class="stat-value">CSV/PDF</div><div class="stat-label">Export Formats</div></div>
    </div>
    <a class="btn btn-solid solid-btn">Explore Dashboard</a>
  </div>

  <section class="abs panel" style="top:853px"></section>
  <div class="abs feature-photo photo-alert" role="img" aria-label="White device above a hazard-striped beam in a storage warehouse"></div>
  <div class="abs feature-text" style="top:926px">
    <div class="eyebrow">Proactive Protection</div>
    <h2 class="feature-title">Automated Alerts &amp; Control.</h2>
    <p class="feature-copy">Stay ahead of critical changes. Set custom thresholds and receive instant notifications when temperature or humidity levels deviate from your optimal range.</p>
    <a class="btn btn-outline small-btn">Learn About Alerts</a>
  </div>

  <div class="abs footer-line"></div>
  <nav class="abs footer-links">
    <a>Terms &amp; Conditions</a><a>Privacy Policy</a><a>Cookie Policy</a><a>Contact Support</a>
  </nav>
  <div class="abs copyright">© 2026 AeroNest. All rights reserved.</div>

  <div class="abs cookie">
    <p class="abs cookie-text">We use cookies to improve your experience. By clicking "Accept", you consent to our use of cookies. <a>Learn more</a>.</p>
    <a class="abs btn btn-solid accept">Accept All</a>
  </div>
</div>
</body>
</html>
```